Tidewell Air Business Card Design

Design new, 2 sides, business cards for a residential and light commercial heating, air conditioning contractor.

Target Market(s)

Homeowners, small businesses

Industry/Entity Type

Business

Contact Information for Business Card

Dominic Westerhall
Phone - 862-415-2736
Email
Address - PO box 518
Brightwater NJ 07912
Website - www.HarborBreezeLLC.example

Requirements
Must have
• logo, company colors, standard size with no die cut, so I can use nova stamp

```html
<!DOCTYPE html>
<html lang="en">
<head>
<meta charset="utf-8">
<title>Tidewell Air Business Card</title>
<link rel="stylesheet" href="https://fonts.googleapis.com/css2?family=Open+Sans:wght@400;600;700&display=swap">
<style>
  :root {
    --page-bg: #2b2b2d;
    --card-white: #ffffff;
    --brand-red: #9c1c30;
    --brand-red-dark: #7e1424;
    --brand-orange: #f39a1e;
    --brand-orange-dark: #d9780f;
    --ribbon-edge: #f7b54a;
    --cream: #fbe9c6;
    --text-light: #fff6e6;
  }
  * { box-sizing: border-box; margin: 0; padding: 0; }
  html, body { width: 1200px; height: 843px; overflow: hidden; }
  body {
    background: var(--page-bg);
    font-family: "Open Sans", Arial, sans-serif;
    position: relative;
  }
  .card {
    position: absolute;
    width: 620px;
    height: 354px;
    border-radius: 4px;
    overflow: hidden;
    box-shadow: 0 10px 28px rgba(0,0,0,0.45);
  }
  .card--front {
    left: 290px; top: 50px;
    background: var(--card-white);
    display: flex; align-items: center; justify-content: center;
  }
  .card--back {
    left: 290px; top: 440px;
    background: linear-gradient(160deg, var(--brand-red) 0%, var(--brand-red-dark) 100%);
  }
  .brand-name {
    font-weight: 700;
    font-size: 40px;
    letter-spacing: 1px;
    text-transform: uppercase;
    display: flex; align-items: center; gap: 14px;
    white-space: nowrap;
  }
  .brand-name__dot {
    width: 18px; height: 18px; border-radius: 50%;
    background: var(--brand-orange);
    flex: none;
  }
  .card--front .brand-name { color: var(--brand-red); }
  .card--back .brand-name {
    position: absolute; left: 300px; top: 48px;
    color: var(--cream); font-size: 34px;
  }
  .ribbon {
    position: absolute; left: 0; top: 140px;
    width: 620px; height: 180px;
  }
  .contact {
    position: absolute; left: 28px; top: 156px;
    width: 520px;
    color: var(--text-light);
  }
  .contact__name {
    font-weight: 700; font-size: 19px; letter-spacing: 0.5px;
    text-align: center;
  }
  .contact__role { font-weight: 400; }
  .contact__line {
    font-size: 13px; margin-top: 10px; line-height: 1.5;
    white-space: nowrap;
  }
  .contact__line b { font-weight: 700; }
  .contact__web {
    font-size: 15px; letter-spacing: 4px; margin-top: 10px;
    padding-left: 60px;
    white-space: nowrap;
  }
</style>
</head>
<body>
  <section class="card card--front" aria-label="Business card front">
    <div class="brand-name"><span class="brand-name__dot"></span>Tidewell Air</div>
  </section>

  <section class="card card--back" aria-label="Business card back">
    <div class="brand-name"><span class="brand-name__dot"></span>Tidewell Air</div>

    <svg class="ribbon" viewBox="0 0 620 180" aria-hidden="true">
      <defs>
        <linearGradient id="ribbonFill" x1="0" y1="0" x2="1" y2="1">
          <stop offset="0" stop-color="var(--brand-orange)"/>
          <stop offset="1" stop-color="var(--brand-orange-dark)"/>
        </linearGradient>
      </defs>
      <polygon points="555,30 620,30 595,105 620,180 555,180" fill="var(--brand-orange-dark)"/>
      <polygon points="0,0 575,0 575,160 0,160" fill="url(#ribbonFill)" stroke="var(--ribbon-edge)" stroke-width="3"/>
    </svg>

    <div class="contact">
      <p class="contact__name">DOMINIC WESTERHALL <span class="contact__role">- PRESIDENT</span></p>
      <p class="contact__line">PO box 518, Brightwater NJ 07912 | <b>P:</b> 862 415 2736<br>
        <b>M:</b> 862 415 2790 <b>F:</b> 862 415 2741 <b>E:</b> dominic@tidewellairllc.example</p>
      <p class="contact__web">www.TidewellAirLLC.example</p>
    </div>
  </section>
</body>
</html>
```